New Webpage for High Class Expert Witness Services Company

We are looking for a minimalist design for a webpage that just has our logo and an entry form offer to connect with one of our Liaisons.
The entry form should just ask for Name, Email, Contact Info and Description of Project.

Company Name is: The Marlowe Crest Advisory Services

Number of Pages Required

1 page

```html
<!DOCTYPE html>
<html lang="en">
<head>
<meta charset="utf-8">
<title>The Marlowe Crest Advisory Services — Consultation</title>
<link href="https://fonts.googleapis.com/css2?family=Cinzel:wght@600;700&family=Inter:wght@400;500&display=swap" rel="stylesheet">
<style>
  :root {
    --bg-dark: #1b1b1b;
    --bg-mid: #3b3b3b;
    --card: #f7f7f7;
    --field: #ececec;
    --ink: #1c1c1c;
    --ink-soft: #5e5e5e;
    --ink-muted: #6a6a6a;
    --logo: #d2d2d2;
    --logo-dim: #b9b9b9;
    --footer: #ffffff;
  }
  * { box-sizing: border-box; margin: 0; padding: 0; }
  html, body { width: 1200px; height: 813px; overflow: hidden; }
  body {
    position: relative;
    background: radial-gradient(ellipse at 50% 0%, var(--bg-mid) 0%, var(--bg-dark) 70%);
    font-family: "Inter", sans-serif;
  }
  .brand {
    position: absolute; left: 0; top: 62px; width: 1200px;
    display: flex; flex-direction: column; align-items: center;
  }
  .brand-row { display: flex; align-items: center; gap: 16px; }
  .brand-mark { width: 34px; height: 34px; background: var(--logo); }
  .brand-name {
    font-family: "Cinzel", serif; font-weight: 600; font-size: 36px;
    letter-spacing: 2px; color: var(--logo);
  }
  .brand-tagline {
    margin-top: 30px; font-family: "Cinzel", serif; font-weight: 600;
    font-size: 15px; letter-spacing: 4.5px; color: var(--logo-dim);
  }
  .card {
    position: absolute; left: 111px; top: 221px; width: 977px; height: 520px;
    background: var(--card); border-radius: 34px; overflow: hidden;
  }
  .card-photo {
    position: absolute; left: 0; top: 0; width: 100%; height: 100%;
    background:
      radial-gradient(ellipse 160px 220px at 330px 380px, rgba(150,150,150,0.35), transparent 70%),
      radial-gradient(ellipse 420px 300px at 250px 300px, rgba(210,210,210,0.6), transparent 75%),
      linear-gradient(90deg, #eeeeee 0%, #f6f6f6 55%, #f2f2f2 100%);
  }
  .intro { position: absolute; left: 48px; top: 52px; width: 440px; }
  .intro-kicker {
    font-family: "Cinzel", serif; font-weight: 700; font-size: 22px;
    color: var(--ink-muted); letter-spacing: 0.5px;
  }
  .intro-title {
    margin-top: 6px; font-family: "Cinzel", serif; font-weight: 700;
    font-size: 41px; line-height: 47px; color: var(--ink);
  }
  .intro-text {
    margin-top: 10px; max-width: 385px; font-size: 16.5px; line-height: 32px; color: var(--ink-soft);
  }
  .consult-form { position: absolute; left: 523px; top: 52px; width: 405px; height: 420px; }
  .field {
    position: relative; height: 51px; margin-bottom: 21px;
    background: var(--field); border-radius: 10px;
    box-shadow: 0 2px 6px rgba(0,0,0,0.05);
    display: flex; align-items: center; padding: 0 26px;
    font-size: 15px; color: #555;
  }
  .field-area { height: 128px; align-items: flex-start; padding-top: 20px; margin-bottom: 0;
    background: linear-gradient(180deg, #ececec, #e4e4e4); }
  .field svg { position: absolute; right: 26px; top: 17px; width: 16px; height: 16px; fill: #4a4a4a; }
  .submit {
    position: absolute; right: 0; top: 373px; width: 194px; height: 43px;
    border: 1px solid #bdbdbd; border-radius: 8px;
    background: linear-gradient(180deg, #ededed, #c8c8c8);
    box-shadow: 0 10px 24px rgba(0,0,0,0.15);
    font-family: "Inter", sans-serif; font-size: 16px; color: #111;
    white-space: nowrap;
  }
  .footer {
    position: absolute; left: 0; top: 770px; width: 1200px; text-align: center;
    font-size: 15px; font-weight: 500; color: var(--footer);
  }
</style>
</head>
<body>
  <header class="brand">
    <div class="brand-row">
      <span class="brand-mark"></span>
      <span class="brand-name">MARLOWE CREST ADVISORY SERVICES</span>
    </div>
    <div class="brand-tagline">SEAMLESS MEDICAL EXPERT INTEGRATION</div>
  </header>

  <main class="card">
    <div class="card-photo" role="img" aria-label="Soft black and white photo of a doctor holding a stethoscope"></div>

    <section class="intro">
      <p class="intro-kicker">PRECISION. CREDIBILITY.</p>
      <h1 class="intro-title">DEFENSE WITHOUT COMPROMISE.</h1>
      <p class="intro-text">Connect with a dedicated liaison to engage highly qualified expert witnesses for complex, high-stakes matters.</p>
    </section>

    <form class="consult-form">
      <div class="field">Full Name
        <svg viewBox="0 0 16 16"><circle cx="8" cy="5" r="3.3"/><path d="M2 15c0-3.6 2.7-5.5 6-5.5s6 1.9 6 5.5z"/></svg>
      </div>
      <div class="field">Email Address
        <svg viewBox="0 0 16 16"><path d="M1 3h14v10H1z M2.2 4.2 8 8.6l5.8-4.4v-.2H2.2z" fill-rule="evenodd"/></svg>
      </div>
      <div class="field">Contact Number
        <svg viewBox="0 0 16 16"><path d="M1 6c0-2 3-3.5 7-3.5S15 4 15 6v1.3h-3.3V5.8H4.3v1.5H1z"/><path d="M4 8h8l2 6H2z M8 9.5a2 2 0 1 0 0 4 2 2 0 0 0 0-4z" fill-rule="evenodd"/></svg>
      </div>
      <div class="field field-area">Project Overview
        <svg viewBox="0 0 16 16"><path d="M6.5 1.5C3.4 1.5 1 3.5 1 6c0 1.3.6 2.4 1.7 3.2L2 12l3-1.7c.5.1 1 .2 1.5.2 3.1 0 5.5-2 5.5-4.5S9.6 1.5 6.5 1.5z"/><path d="M13.3 6.5c1.1.8 1.7 1.9 1.7 3.1 0 1-.4 1.9-1.1 2.6l.6 2.3-2.6-1.4c-.5.1-1 .2-1.5.2-1.6 0-3-.6-3.9-1.5 3.3-.2 6.2-2.3 6.8-5.3z"/></svg>
      </div>
      <button type="button" class="submit">Initiate Consultation</button>
    </form>
  </main>

  <footer class="footer">(C) Copyright 2026 | All Rights Reserved</footer>
</body>
</html>
```